Sophisticated, clean website reflecting my feminine, playful side to sell my abstract art,

I need a website no more than 3 pages to showcase my paintings, a little about me and some contact info. I do abstracts so looking for something a little edgy, yet feminine and current.
Updates

Hi there, These are some artists websites that I Iike: Marnelvoss.com (I like how airy it is) peterwallombry.com garethpolvens.com (I like how it scrolls) I'll need a place for a photo ( a headshot-i do not have it yet so I'll need to be able to upload that later) as well as an area for my bio. Also, it's important that I will be able to upload any new photos and descriptions easily so it should be user friendly. Lastly, I like in a sunny place so would like to have this seem upbeat and playful as that is how i like to paint. thanks-I'm trying to upload my photos now -

Target Market(s)

ppl ages 35-70 who want large scale art for their homes

Industry/Entity Type

art

Coding

Coded - Design and coding required

Number of Pages Required

3 page

Colors

Designer to choose colors to be used in the design.

Requirements
Must have
• photos of my art, a place for my bio, be easy to reach me. tasteful-nothing too "in your face" -my clients are pretty high end and organized. They like clean lines
Nice to have
• sophisticated background, muted tones in the back-similar clean font throughout-no cursive
Should not have
• too many dark areas. Too many blocks of color. Too serious.

```html
<!DOCTYPE html>
<html lang="en">
<head>
<meta charset="utf-8">
<title>Lydia Marrow — Abstract Art</title>
<link href="https://fonts.googleapis.com/css2?family=Playfair+Display:wght@600&family=Poppins:wght@500&family=Tinos&display=swap" rel="stylesheet">
<style>
  :root {
    --ink: #111111;
    --muted: #666666;
    --rule: #c9c9c9;
    --gold: #b9ad84;
    --footer-bg: #f8f8f8;
    --page-bg: #ffffff;
  }
  * { box-sizing: border-box; margin: 0; padding: 0; }
  html, body { width: 1075px; height: 1200px; overflow: hidden; background: var(--page-bg); }
  .site { position: relative; width: 1075px; height: 1200px; }

  .brand-mark {
    position: absolute; left: 492px; top: 8px; width: 92px; height: 88px;
    border: 4px solid var(--gold); background: var(--page-bg);
  }
  .brand-name {
    position: absolute; left: 0; right: 0; top: 98px; text-align: center;
    font-family: 'Playfair Display', serif; font-weight: 600; font-size: 32px;
    color: var(--ink); line-height: 44px;
  }
  .header-rule { position: absolute; left: 0; right: 0; top: 150px; height: 1px; background: var(--rule); }

  .main-nav { position: absolute; top: 172px; left: 0; right: 0; height: 24px; }
  .main-nav a {
    position: absolute; transform: translateX(-50%); white-space: nowrap;
    font-family: 'Poppins', sans-serif; font-weight: 500; font-size: 16px;
    color: var(--muted); text-decoration: none; letter-spacing: 0.2px;
  }
  .main-nav a.is-current { color: var(--ink); }

  .feature-artwork {
    position: absolute; left: 90px; top: 225px; width: 895px; height: 598px;
    background: linear-gradient(160deg, #e2c47a 0%, #ece6d8 45%, #9fb4d2 100%);
  }
  .slider-arrow { position: absolute; top: 512px; width: 24px; height: 24px; }
  .slider-arrow.prev { left: 59px; }
  .slider-arrow.next { left: 993px; }

  .thumb-row { position: absolute; top: 838px; left: 90px; width: 896px; height: 159px; }
  .thumb { position: absolute; top: 0; width: 168px; height: 159px; }
  .thumb-1 { left: 0;   background: linear-gradient(180deg, #c9a57c, #b07a5a); }
  .thumb-2 { left: 182px; background: linear-gradient(180deg, #cdb3a8, #8f6a60); }
  .thumb-3 { left: 364px; background: linear-gradient(180deg, #5f7a68, #3a4a44); }
  .thumb-4 { left: 546px; background: linear-gradient(180deg, #c8b69c, #a9bfc9); }
  .thumb-5 { left: 728px; background: linear-gradient(180deg, #9fb9b3, #4f9a8e); }

  .site-footer { position: absolute; left: 0; right: 0; top: 1069px; bottom: 0; background: var(--footer-bg); }
  .social-link {
    position: absolute; top: 36px; width: 34px; height: 34px; border: 1px solid var(--ink); border-radius: 50%;
    display: flex; align-items: center; justify-content: center;
    font-family: 'Poppins', sans-serif; font-weight: 500; font-size: 8px; color: var(--ink); text-decoration: none;
  }
  .copyright {
    position: absolute; left: 0; right: 0; top: 89px; text-align: center;
    font-family: 'Tinos', serif; font-size: 14px; color: var(--ink);
  }
</style>
</head>
<body>
<div class="site">
  <header>
    <div class="brand-mark" aria-hidden="true"></div>
    <h1 class="brand-name">Lydia Marrow</h1>
    <div class="header-rule"></div>
    <nav class="main-nav">
      <a href="#" class="is-current" style="left:301px">HOME</a>
      <a href="#" style="left:448px">ABOUT ME</a>
      <a href="#" style="left:603px">GALLERY</a>
      <a href="#" style="left:758px">CONTACT</a>
    </nav>
  </header>

  <main>
    <svg class="slider-arrow prev" viewBox="0 0 24 24" aria-label="Previous">
      <path d="M23 12H2M11 3L2 12l9 9" fill="none" stroke="#111" stroke-width="1.6"/>
    </svg>
    <div class="feature-artwork" role="img" aria-label="Featured abstract painting in gold, blue and rust tones"></div>
    <svg class="slider-arrow next" viewBox="0 0 24 24" aria-label="Next">
      <path d="M1 12h21M13 3l9 9-9 9" fill="none" stroke="#111" stroke-width="1.6"/>
    </svg>

    <div class="thumb-row">
      <div class="thumb thumb-1" role="img" aria-label="Abstract painting in warm red tones"></div>
      <div class="thumb thumb-2" role="img" aria-label="Abstract painting in pink and plum tones"></div>
      <div class="thumb thumb-3" role="img" aria-label="Abstract painting in orange, teal and black"></div>
      <div class="thumb thumb-4" role="img" aria-label="Abstract painting in pale blue tones"></div>
      <div class="thumb thumb-5" role="img" aria-label="Abstract painting in lavender, cream and teal"></div>
    </div>
  </main>

  <footer class="site-footer">
    <a href="#" class="social-link" style="left:481px">Vela</a>
    <a href="#" class="social-link" style="left:520px">Tuno</a>
    <a href="#" class="social-link" style="left:560px">Ilka</a>
    <p class="copyright">©Copyright ©2022 Lydia Marrow Art. All Rights Reserved.</p>
  </footer>
</div>
</body>
</html>
```